Annual Report Velomar 2025

Take a PowerPoint presentation and turn it into a info graphic type annual report, posters and flyers.

Annual report ideally no more than 8 pages.

Please use the colours and fonts in the attached brand guidelines.

We are looking for an infographic visually appealing piece.

```html
<!DOCTYPE html>
<html lang="en">
<head>
<meta charset="utf-8">
<title>Velomar 2026 Annual Report – Slide Set</title>
<link href="https://fonts.googleapis.com/css2?family=Poppins:wght@400;500;600;700&display=swap" rel="stylesheet">
<style>
:root{
  --navy:#1b3461;
  --navy-deep:#14284c;
  --green:#7aa43a;
  --green-dark:#3f6a1f;
  --green-pale:#e4f3c8;
  --page:#ababab;
  --white:#ffffff;
  --ink:#1d1d1d;
  --rule:#c9ced8;
  --card:#ececec;
}
*{margin:0;padding:0;box-sizing:border-box}
html,body{width:1200px;height:1187px;overflow:hidden;background:var(--page)}
body{font-family:'Poppins',sans-serif;color:var(--ink)}
.canvas{position:relative;width:1200px;height:1187px;background:var(--page)}
.slide{position:absolute;width:325px;height:183px;overflow:hidden;background:var(--white)}
.slide.navy{background:var(--navy)}
.abs{position:absolute}
.col1{left:84.5px}.col2{left:437px}.col3{left:791px}
.row1{top:69.6px}.row2{top:285px}.row3{top:501px}.row4{top:718px}.row5{top:934px}

.brand{position:absolute;font-weight:600;color:var(--navy);display:flex;align-items:center;gap:3px;line-height:1}
.brand .dot{display:inline-block;border-radius:50%;background:var(--green)}
.brand.light{color:var(--white)}
.cover-brand{font-size:17px}
.cover-brand .dot{width:12px;height:12px}
.kicker{position:absolute;font-size:8.4px;font-weight:500;color:var(--green);letter-spacing:.1px}
.title{position:absolute;font-size:17.5px;font-weight:700;line-height:18.4px;color:var(--navy);text-transform:uppercase}
.title .hl{color:var(--green)}
.navy .title{color:var(--white)}
.url{position:absolute;font-size:5.6px;font-weight:500;color:var(--ink)}
.navy .url{color:var(--white)}

.heading{position:absolute;left:13px;top:12px;font-size:11px;font-weight:600;color:var(--navy)}
.on-dark .heading,.on-dark .body{color:var(--white)}
.body{position:absolute;font-size:4.2px;line-height:5.4px;text-align:justify;color:var(--ink)}
.body p{margin-bottom:5px}
.footer-rule{position:absolute;left:13px;right:50px;top:169px;height:.6px;background:var(--navy)}
.on-dark .footer-rule{background:var(--white)}
.footer-brand{right:13px;top:166px;font-size:6.2px}
.footer-brand .dot{width:5px;height:5px}

.toc-title{position:absolute;left:17px;top:18px;font-size:14.5px;font-weight:600;line-height:15px;color:var(--navy)}
.toc-title .hl{color:var(--green)}
.toc-note{position:absolute;left:171px;top:18px;width:138px;height:33px;background:#f0f0f0;padding:6px 5px;font-size:3.7px;line-height:4.6px;font-weight:600;color:var(--navy)}
.toc-item{position:absolute;width:136px;height:20px;border-bottom:.6px dashed #9a9a9a}
.toc-item .name{font-size:4.7px;font-weight:500;color:var(--green)}
.toc-item .sum{font-size:3.7px;font-weight:500;color:var(--navy);margin-top:2px}
.toc-item .num{position:absolute;right:0;top:4px;font-size:4.4px;font-weight:600;color:var(--navy)}

.checks{position:absolute;left:13px;top:104px;width:300px;display:grid;grid-template-columns:repeat(3,1fr);row-gap:6.3px}
.check{display:flex;align-items:center;gap:2px;font-size:4.8px;color:var(--navy)}
.check svg{width:6px;height:6px}
.sub{position:absolute;left:12px;top:31px;font-size:6.6px;font-weight:500;color:var(--navy)}

.photo{position:absolute}
.proc-title{position:absolute;left:0;right:0;top:28px;text-align:center;font-size:11.5px;font-weight:500;color:var(--navy);letter-spacing:.3px}
.proc-title small{font-size:3.6px;letter-spacing:1.6px;vertical-align:6px;margin-left:1px;border-bottom:.5px solid var(--navy)}
.step-label{position:absolute;width:50px;text-align:center}
.step-label b{display:block;font-size:4.4px;font-weight:600;color:var(--navy)}
.step-label span{display:block;font-size:2.9px;line-height:3.6px;color:#9a9a9a;margin-top:2px}
</style>
</head>
<body>
<main class="canvas">

<!-- Row 1: covers -->
<section class="slide col1 row1">
  <div class="brand cover-brand" style="left:17px;top:17px"><span class="dot"></span>Velomar</div>
  <div class="kicker" style="left:17px;top:71px">2026 ANNUAL REPORT</div>
  <h1 class="title" style="left:17px;top:80px">Resilience<br><span class="hl">Through</span><br>Partnership</h1>
  <div class="url" style="left:16px;top:165px">www.velomar.org</div>
  <div class="photo" style="left:165px;top:0;width:160px;height:183px;background:var(--navy);border-radius:90px 0 0 90px"></div>
  <div class="photo" role="img" aria-label="Photo of volunteers tinted green" style="left:190px;top:20px;width:135px;height:163px;background:linear-gradient(150deg,#8fb955,#5f8f2c);border-radius:70px 0 0 70px"></div>
</section>

<section class="slide navy col2 row1">
  <div class="brand light cover-brand" style="left:17px;top:17px"><span class="dot"></span>Velomar</div>
  <div class="kicker" style="left:17px;top:71px">2026 ANNUAL REPORT</div>
  <h1 class="title" style="left:17px;top:80px">Resilience<br><span class="hl">Through</span><br>Partnership</h1>
  <div class="url" style="left:16px;top:165px">www.velomar.org</div>
  <div class="photo" role="img" aria-label="Photo of a smiling senior couple tinted green" style="left:170px;top:18px;width:155px;height:165px;background:linear-gradient(150deg,#9ec062,#5f8f2c);border-radius:80px 0 0 0"></div>
</section>

<section class="slide navy col3 row1">
  <div class="brand light cover-brand" style="left:116px;top:17px"><span class="dot"></span>Velomar</div>
  <svg class="abs" style="left:0;top:0" width="325" height="183" viewBox="0 0 325 183">
    <path role="img" aria-label="Photo of a pile of coins" d="M0,46 L325,46 L325,138 Q162,60 0,138 Z" fill="url(#coins)"/>
    <path d="M0,138 Q162,60 325,138" fill="none" stroke="var(--green)" stroke-width="2"/>
    <defs><linearGradient id="coins" x1="0" y1="0" x2="1" y2="1"><stop offset="0" stop-color="#8a6a52"/><stop offset=".5" stop-color="#b98a66"/><stop offset="1" stop-color="#6f5a4a"/></linearGradient></defs>
  </svg>
  <div class="kicker" style="left:0;right:0;text-align:center;top:112px">2026 ANNUAL REPORT</div>
  <h1 class="title" style="left:0;right:0;text-align:center;top:122px">Resilience <span class="hl">Through</span><br>Partnership</h1>
  <div class="url" style="left:0;right:0;text-align:center;top:165px">www.velomar.org</div>
</section>

<!-- Row 2 -->
<section class="slide col1 row2">
  <h2 class="toc-title">Table of<br><span class="hl">Contents</span></h2>
  <div class="toc-note">Here You Can Add Some Brief Text to Explain The Title This is Just a Demo So Consider Replacing This Text with Your Own Presentation Content. It is Highly Recommended That You Replace This Demo Text</div>
  <div class="toc-item" style="left:17px;top:66px"><div class="name">Welcome Slide</div><div class="sum">Write a Short Summary for this Slide</div><div class="num">01</div></div>
  <div class="toc-item" style="left:17px;top:91px"><div class="name">About Us</div><div class="sum">Write a Short Summary for this Slide</div><div class="num">02</div></div>
  <div class="toc-item" style="left:17px;top:116px"><div class="name">Mission &amp; Vision</div><div class="sum">Write a Short Summary for this Slide</div><div class="num">03</div></div>
  <div class="toc-item" style="left:17px;top:141px"><div class="name">Our History</div><div class="sum">Write a Short Summary for this Slide</div><div class="num">04</div></div>
  <div class="toc-item" style="left:173px;top:66px"><div class="name">Pricing Slide</div><div class="sum">Write a Short Summary for this Slide</div><div class="num">05</div></div>
  <div class="toc-item" style="left:173px;top:91px"><div class="name">Our Infographics</div><div class="sum">Write a Short Summary for this Slide</div><div class="num">06</div></div>
  <div class="toc-item" style="left:173px;top:116px"><div class="name">Client Reviews</div><div class="sum">Write a Short Summary for this Slide</div><div class="num">07</div></div>
  <div class="toc-item" style="left:173px;top:141px"><div class="name">Data &amp; Charts</div><div class="sum">Write a Short Summary for this Slide</div><div class="num">08</div></div>
</section>

<section class="slide navy col2 row2">
  <div class="photo" role="img" aria-label="Photo of hands reviewing financial charts at a desk, navy tint" style="inset:0;background:radial-gradient(circle at 45% 60%,#2c4470,#17294c 75%)"></div>
  <div class="brand light" style="left:100px;top:80px;font-size:22px"><span class="dot" style="width:17px;height:17px"></span>Velomar</div>
</section>

<section class="slide col3 row2">
  <h2 class="heading">Heading Goes Here</h2>
  <div class="body" style="left:13px;top:28px;width:299px">
    <p>Lorem ipsum dolor sit amet, consectetuer adipiscing elit, sed diam nonummy nibh euismod tincidunt ut laoreet dolore magna aliquam erat volutpat. Ut wisi enim ad minim veniam, quis nostrud exerci tation ullamcorper suscipit lobortis nisl ut aliquip ex ea commodo consequat. Duis autem vel eum iriure dolor in hendrerit in vulputate velit esse molestie consequat, vel illum dolore eu feugiat nulla facilisis at vero eros et accumsan et iusto odio dignissim qui blandit praesent luptatum zzril delenit augue duis dolore te feugait nulla facilisi.</p>
    <p>Lorem ipsum dolor sit amet, cons ectetuer adipiscing elit, sed diam nonummy nibh euismod tincidunt ut laoreet dolore magna aliquam erat volutpat. Ut wisi enim ad minim veniam, quis nostrud exerci tation ullamcorper suscipit lobortis nisl ut aliquip ex ea commodo consequat.</p>
  </div>
  <h2 class="heading" style="top:85px">Heading Goes Here</h2>
  <div class="checks">
    <div class="check"><svg viewBox="0 0 10 10"><circle cx="5" cy="5" r="4.2" fill="none" stroke="var(--green)" stroke-width="1.2"/><path d="M3 5.2l1.5 1.5L7.2 3.8" fill="none" stroke="var(--green)" stroke-width="1.2"/></svg>Lorem ipsum dolor sit amet</div>
    <div class="check"><svg viewBox="0 0 10 10"><circle cx="5" cy="5" r="4.2" fill="none" stroke="var(--green)" stroke-width="1.2"/><path d="M3 5.2l1.5 1.5L7.2 3.8" fill="none" stroke="var(--green)" stroke-width="1.2"/></svg>Lorem ipsum dolor sit amet</div>
    <div class="check"><svg viewBox="0 0 10 10"><circle cx="5" cy="5" r="4.2" fill="none" stroke="var(--green)" stroke-width="1.2"/><path d="M3 5.2l1.5 1.5L7.2 3.8" fill="none" stroke="var(--green)" stroke-width="1.2"/></svg>Lorem ipsum dolor sit amet</div>
    <div class="check"><svg viewBox="0 0 10 10"><circle cx="5" cy="5" r="4.2" fill="none" stroke="var(--green)" stroke-width="1.2"/><path d="M3 5.2l1.5 1.5L7.2 3.8" fill="none" stroke="var(--green)" stroke-width="1.2"/></svg>Lorem ipsum dolor sit amet</div>
    <div class="check"><svg viewBox="0 0 10 10"><circle cx="5" cy="5" r="4.2" fill="none" stroke="var(--green)" stroke-width="1.2"/><path d="M3 5.2l1.5 1.5L7.2 3.8" fill="none" stroke="var(--green)" stroke-width="1.2"/></svg>Lorem ipsum dolor sit amet</div>
    <div class="check"><svg viewBox="0 0 10 10"><circle cx="5" cy="5" r="4.2" fill="none" stroke="var(--green)" stroke-width="1.2"/><path d="M3 5.2l1.5 1.5L7.2 3.8" fill="none" stroke="var(--green)" stroke-width="1.2"/></svg>Lorem ipsum dolor sit amet</div>
    <div class="check"><svg viewBox="0 0 10 10"><circle cx="5" cy="5" r="4.2" fill="none" stroke="var(--green)" stroke-width="1.2"/><path d="M3 5.2l1.5 1.5L7.2 3.8" fill="none" stroke="var(--green)" stroke-width="1.2"/></svg>Lorem ipsum dolor sit amet</div>
    <div class="check"><svg viewBox="0 0 10 10"><circle cx="5" cy="5" r="4.2" fill="none" stroke="var(--green)" stroke-width="1.2"/><path d="M3 5.2l1.5 1.5L7.2 3.8" fill="none" stroke="var(--green)" stroke-width="1.2"/></svg>Lorem ipsum dolor sit amet</div>
    <div class="check"><svg viewBox="0 0 10 10"><circle cx="5" cy="5" r="4.2" fill="none" stroke="var(--green)" stroke-width="1.2"/><path d="M3 5.2l1.5 1.5L7.2 3.8" fill="none" stroke="var(--green)" stroke-width="1.2"/></svg>Lorem ipsum dolor sit amet</div>
    <div class="check"><svg viewBox="0 0 10 10"><circle cx="5" cy="5" r="4.2" fill="none" stroke="var(--green)" stroke-width="1.2"/><path d="M3 5.2l1.5 1.5L7.2 3.8" fill="none" stroke="var(--green)" stroke-width="1.2"/></svg>Lorem ipsum dolor sit amet</div>
    <div class="check"><svg viewBox="0 0 10 10"><circle cx="5" cy="5" r="4.2" fill="none" stroke="var(--green)" stroke-width="1.2"/><path d="M3 5.2l1.5 1.5L7.2 3.8" fill="none" stroke="var(--green)" stroke-width="1.2"/></svg>Lorem ipsum dolor sit amet</div>
    <div class="check"><svg viewBox="0 0 10 10"><circle cx="5" cy="5" r="4.2" fill="none" stroke="var(--green)" stroke-width="1.2"/><path d="M3 5.2l1.5 1.5L7.2 3.8" fill="none" stroke="var(--green)" stroke-width="1.2"/></svg>Lorem ipsum dolor sit amet</div>
  </div>
  <div class="footer-rule"></div>
  <div class="brand footer-brand"><span class="dot"></span>Velomar</div>
</section>

<!-- Row 3: two-column text -->
<section class="slide col1 row3">
  <h2 class="heading">Heading Goes Here</h2>
  <div class="body" style="left:13px;top:29px;width:143px">
    <p>Lorem ipsum dolor sit amet, consectetuer adipiscing elit, sed diam nonummy nibh euismod tincidunt ut laoreet dolore magna aliquam erat volutpat. Ut wisi enim ad minim veniam, quis nostrud exerci tation ullamcorper suscipit lobortis nisl ut aliquip ex ea commodo consequat. Duis autem vel eum iriure dolor in hendrerit in vulputate velit esse molestie consequat, vel illum dolore eu feugiat nulla facilisis at vero eros et accumsan et iusto odio dignissim qui blandit praesent luptatum zzril delenit augue duis dolore te feugait nulla facilisi.</p>
    <p>Lorem ipsum dolor sit amet, cons ectetuer adipiscing elit, sed diam nonummy nibh euismod tincidunt ut laoreet dolore magna aliquam erat volutpat. Ut wisi enim ad minim veniam, quis nostrud exerci tation ullamcorper suscipit lobortis nisl ut aliquip ex ea commodo consequat.</p>
    <p>Lorem ipsum dolor sit amet, cons ectetuer adipiscing elit, sed diam nonummy nibh euismod tincidunt ut laoreet dolore magna aliquam erat volutpat. Ut wisi enim ad minim veniam, quis nostrud exerci tation ullamcorper suscipit lobortis nisl ut aliquip ex ea commodo consequat.</p>
  </div>
  <div class="body" style="left:169px;top:29px;width:143px">
    <p>Lorem ipsum dolor sit amet, consectetuer adipiscing elit, sed diam nonummy nibh euismod tincidunt ut laoreet dolore magna aliquam erat volutpat. Ut wisi enim ad minim veniam, quis nostrud exerci tation ullamcorper suscipit lobortis nisl ut aliquip ex ea commodo consequat. Duis autem vel eum iriure dolor in hendrerit in vulputate velit esse molestie consequat, vel illum dolore eu feugiat nulla facilisis at vero eros et accumsan et iusto odio dignissim qui blandit praesent luptatum zzril delenit augue duis dolore te feugait nulla facilisi.</p>
    <p>Lorem ipsum dolor sit amet, cons ectetuer adipiscing elit, sed diam nonummy nibh euismod tincidunt ut laoreet dolore magna aliquam erat volutpat. Ut wisi enim ad minim veniam, quis nostrud exerci tation ullamcorper suscipit lobortis nisl ut aliquip ex ea commodo consequat.</p>
    <p>Lorem ipsum dolor sit amet, cons ectetuer adipiscing elit, sed diam nonummy nibh euismod tincidunt ut laoreet dolore magna aliquam erat volutpat. Ut wisi enim ad minim veniam, quis nostrud exerci tation ullamcorper suscipit lobortis nisl ut aliquip ex ea commodo consequat.</p>
  </div>
  <div class="footer-rule"></div>
  <div class="brand footer-brand"><span class="dot"></span>Velomar</div>
</section>

<section class="slide navy on-dark col2 row3">
  <div class="photo" role="img" aria-label="Photo of business meeting, navy tint" style="inset:0;background:radial-gradient(circle at 60% 40%,#233b66,#14284c 80%)"></div>
  <h2 class="heading">Heading Goes Here</h2>
  <div class="body" style="left:13px;top:29px;width:143px">
    <p>Lorem ipsum dolor sit amet, consectetuer adipiscing elit, sed diam nonummy nibh euismod tincidunt ut laoreet dolore magna aliquam erat volutpat. Ut wisi enim ad minim veniam, quis nostrud exerci tation ullamcorper suscipit lobortis nisl ut aliquip ex ea commodo consequat. Duis autem vel eum iriure dolor in hendrerit in vulputate velit esse molestie consequat, vel illum dolore eu feugiat nulla facilisis at vero eros et accumsan et iusto odio dignissim qui blandit praesent luptatum zzril delenit augue duis dolore te feugait nulla facilisi.</p>
    <p>Lorem ipsum dolor sit amet, cons ectetuer adipiscing elit, sed diam nonummy nibh euismod tincidunt ut laoreet dolore magna aliquam erat volutpat. Ut wisi enim ad minim veniam, quis nostrud exerci tation ullamcorper suscipit lobortis nisl ut aliquip ex ea commodo consequat.</p>
    <p>Lorem ipsum dolor sit amet, cons ectetuer adipiscing elit, sed diam nonummy nibh euismod tincidunt ut laoreet dolore magna aliquam erat volutpat. Ut wisi enim ad minim veniam, quis nostrud exerci tation ullamcorper suscipit lobortis nisl ut aliquip ex ea commodo consequat.</p>
  </div>
  <div class="body" style="left:169px;top:29px;width:143px">
    <p>Lorem ipsum dolor sit amet, consectetuer adipiscing elit, sed diam nonummy nibh euismod tincidunt ut laoreet dolore magna aliquam erat volutpat. Ut wisi enim ad minim veniam, quis nostrud exerci tation ullamcorper suscipit lobortis nisl ut aliquip ex ea commodo consequat. Duis autem vel eum iriure dolor in hendrerit in vulputate velit esse molestie consequat, vel illum dolore eu feugiat nulla facilisis at vero eros et accumsan et iusto odio dignissim qui blandit praesent luptatum zzril delenit augue duis dolore te feugait nulla facilisi.</p>
    <p>Lorem ipsum dolor sit amet, cons ectetuer adipiscing elit, sed diam nonummy nibh euismod tincidunt ut laoreet dolore magna aliquam erat volutpat. Ut wisi enim ad minim veniam, quis nostrud exerci tation ullamcorper suscipit lobortis nisl ut aliquip ex ea commodo consequat.</p>
    <p>Lorem ipsum dolor sit amet, cons ectetuer adipiscing elit, sed diam nonummy nibh euismod tincidunt ut laoreet dolore magna aliquam erat volutpat. Ut wisi enim ad minim veniam, quis nostrud exerci tation ullamcorper suscipit lobortis nisl ut aliquip ex ea commodo consequat.</p>
  </div>
  <div class="footer-rule"></div>
  <div class="brand light footer-brand"><span class="dot"></span>Velomar</div>
</section>

<section class="slide on-dark col3 row3">
  <div class="photo" role="img" aria-label="Photo of stacked coins, green tint" style="inset:0;background:radial-gradient(circle at 50% 50%,#3e6b22,#23461a 85%)"></div>
  <h2 class="heading">Heading Goes Here</h2>
  <div class="body" style="left:13px;top:29px;width:143px">
    <p>Lorem ipsum dolor sit amet, consectetuer adipiscing elit, sed diam nonummy nibh euismod tincidunt ut laoreet dolore magna aliquam erat volutpat. Ut wisi enim ad minim veniam, quis nostrud exerci tation ullamcorper suscipit lobortis nisl ut aliquip ex ea commodo consequat. Duis autem vel eum iriure dolor in hendrerit in vulputate velit esse molestie consequat, vel illum dolore eu feugiat nulla facilisis at vero eros et accumsan et iusto odio dignissim qui blandit praesent luptatum zzril delenit augue duis dolore te feugait nulla facilisi.</p>
    <p>Lorem ipsum dolor sit amet, cons ectetuer adipiscing elit, sed diam nonummy nibh euismod tincidunt ut laoreet dolore magna aliquam erat volutpat. Ut wisi enim ad minim veniam, quis nostrud exerci tation ullamcorper suscipit lobortis nisl ut aliquip ex ea commodo consequat.</p>
    <p>Lorem ipsum dolor sit amet, cons ectetuer adipiscing elit, sed diam nonummy nibh euismod tincidunt ut laoreet dolore magna aliquam erat volutpat. Ut wisi enim ad minim veniam, quis nostrud exerci tation ullamcorper suscipit lobortis nisl ut aliquip ex ea commodo consequat.</p>
  </div>
  <div class="body" style="left:169px;top:29px;width:143px">
    <p>Lorem ipsum dolor sit amet, consectetuer adipiscing elit, sed diam nonummy nibh euismod tincidunt ut laoreet dolore magna aliquam erat volutpat. Ut wisi enim ad minim veniam, quis nostrud exerci tation ullamcorper suscipit lobortis nisl ut aliquip ex ea commodo consequat. Duis autem vel eum iriure dolor in hendrerit in vulputate velit esse molestie consequat, vel illum dolore eu feugiat nulla facilisis at vero eros et accumsan et iusto odio dignissim qui blandit praesent luptatum zzril delenit augue duis dolore te feugait nulla facilisi.</p>
    <p>Lorem ipsum dolor sit amet, cons ectetuer adipiscing elit, sed diam nonummy nibh euismod tincidunt ut laoreet dolore magna aliquam erat volutpat. Ut wisi enim ad minim veniam, quis nostrud exerci tation ullamcorper suscipit lobortis nisl ut aliquip ex ea commodo consequat.</p>
    <p>Lorem ipsum dolor sit amet, cons ectetuer adipiscing elit, sed diam nonummy nibh euismod tincidunt ut laoreet dolore magna aliquam erat volutpat. Ut wisi enim ad minim veniam, quis nostrud exerci tation ullamcorper suscipit lobortis nisl ut aliquip ex ea commodo consequat.</p>
  </div>
  <div class="footer-rule"></div>
  <div class="brand light footer-brand"><span class="dot"></span>Velomar</div>
</section>

<!-- Row 4 -->
<section class="slide col1 row4">
  <h2 class="heading">Heading Goes Here</h2>
  <div class="body" style="left:13px;top:29px;width:143px">
    <p>Lorem ipsum dolor sit amet, consectetuer adipiscing elit, sed diam nonummy nibh euismod tincidunt ut laoreet dolore magna aliquam erat volutpat. Ut wisi enim ad minim veniam, quis nostrud exerci tation ullamcorper suscipit lobortis nisl ut aliquip ex ea commodo consequat. Duis autem vel eum iriure dolor in hendrerit in vulputate velit esse molestie consequat, vel illum dolore eu feugiat nulla facilisis at vero eros et accumsan et iusto odio dignissim qui blandit praesent luptatum zzril delenit augue duis dolore te feugait nulla facilisi.</p>
    <p>Lorem ipsum dolor sit amet, cons ectetuer adipiscing elit, sed diam nonummy nibh euismod tincidunt ut laoreet dolore magna aliquam erat volutpat. Ut wisi enim ad minim veniam, quis nostrud exerci tation ullamcorper suscipit lobortis nisl ut aliquip ex ea commodo consequat.</p>
    <p>Lorem ipsum dolor sit amet, cons ectetuer adipiscing elit, sed diam nonummy nibh euismod tincidunt ut laoreet dolore magna aliquam erat volutpat. Ut wisi enim ad minim veniam, quis nostrud exerci tation ullamcorper suscipit lobortis nisl ut aliquip ex ea commodo consequat.</p>
  </div>
  <div class="photo" role="img" aria-label="Photo of a person analysing stock charts on a laptop" style="left:169px;top:30px;width:143px;height:120px;background:linear-gradient(135deg,#f4f4f4 0%,#d9d9d9 45%,#3a3a3a 100%)"></div>
  <div class="footer-rule"></div>
  <div class="brand footer-brand"><span class="dot"></span>Velomar</div>
</section>

<section class="slide col2 row4">
  <h2 class="heading">Heading Goes Here</h2>
  <div class="photo" role="img" aria-label="Photo of hands reviewing printed charts on a desk" style="left:13px;top:30px;width:143px;height:120px;background:linear-gradient(135deg,#c9a77c 0%,#e8e2d6 50%,#b58e62 100%)"></div>
  <div class="body" style="left:169px;top:29px;width:143px">
    <p>Lorem ipsum dolor sit amet, consectetuer adipiscing elit, sed diam nonummy nibh euismod tincidunt ut laoreet dolore magna aliquam erat volutpat. Ut wisi enim ad minim veniam, quis nostrud exerci tation ullamcorper suscipit lobortis nisl ut aliquip ex ea commodo consequat. Duis autem vel eum iriure dolor in hendrerit in vulputate velit esse molestie consequat, vel illum dolore eu feugiat nulla facilisis at vero eros et accumsan et iusto odio dignissim qui blandit praesent luptatum zzril delenit augue duis dolore te feugait nulla facilisi.</p>
    <p>Lorem ipsum dolor sit amet, cons ectetuer adipiscing elit, sed diam nonummy nibh euismod tincidunt ut laoreet dolore magna aliquam erat volutpat. Ut wisi enim ad minim veniam, quis nostrud exerci tation ullamcorper suscipit lobortis nisl ut aliquip ex ea commodo consequat.</p>
    <p>Lorem ipsum dolor sit amet, cons ectetuer adipiscing elit, sed diam nonummy nibh euismod tincidunt ut laoreet dolore magna aliquam erat volutpat. Ut wisi enim ad minim veniam, quis nostrud exerci tation ullamcorper suscipit lobortis nisl ut aliquip ex ea commodo consequat.</p>
  </div>
  <div class="footer-rule"></div>
  <div class="brand footer-brand"><span class="dot"></span>Velomar</div>
</section>

<section class="slide col3 row4">
  <h2 class="heading">Heading Goes Here</h2>
  <div class="sub">Line Chart</div>
  <svg class="abs" style="left:0;top:0" width="325" height="183" viewBox="0 0 325 183" font-family="Poppins, sans-serif">
    <line x1="13" y1="41" x2="312" y2="41" stroke="#e6e6e6" stroke-width=".5"/>
    <circle cx="267" cy="46" r="1.6" fill="#8c8c8c"/><text x="270" y="47.3" font-size="3.6" fill="#444">Sales</text>
    <circle cx="287" cy="46" r="1.6" fill="var(--navy)"/><text x="290" y="47.3" font-size="3.6" fill="#444">Orders</text>
    <g stroke="#eeeeee" stroke-width=".4">
      <line x1="17" y1="51" x2="310" y2="51"/><line x1="17" y1="61" x2="310" y2="61"/><line x1="17" y1="71" x2="310" y2="71"/><line x1="17" y1="81" x2="310" y2="81"/><line x1="17" y1="91" x2="310" y2="91"/><line x1="17" y1="101" x2="310" y2="101"/><line x1="17" y1="111" x2="310" y2="111"/><line x1="17" y1="121" x2="310" y2="121"/><line x1="17" y1="131" x2="310" y2="131"/><line x1="17" y1="141" x2="310" y2="141"/><line x1="17" y1="151" x2="310" y2="151"/>
    </g>
    <g font-size="2.6" fill="#555" text-anchor="end">
      <text x="15" y="52">100</text><text x="15" y="62">90</text><text x="15" y="72">80</text><text x="15" y="82">70</text><text x="15" y="92">60</text><text x="15" y="102">50</text><text x="15" y="112">40</text><text x="15" y="122">30</text><text x="15" y="132">20</text><text x="15" y="142">10</text><text x="15" y="152">0</text>
    </g>
    <polyline fill="none" stroke="#8c8c8c" stroke-width=".7" points="18,141 42,121 67,131 91,101 116,91 140,111 165,101 189,111 214,71 238,81 263,91 287,71"/>
    <polyline fill="none" stroke="var(--navy)" stroke-width=".8" points="18,111 42,101 67,111 91,81 116,81 140,91 165,81 189,81 214,64 238,61 263,61 287,64 311,61"/>
    <g fill="#8c8c8c"><circle cx="18" cy="141" r="1"/><circle cx="42" cy="121" r="1"/><circle cx="67" cy="131" r="1"/><circle cx="91" cy="101" r="1"/><circle cx="116" cy="91" r="1"/><circle cx="140" cy="111" r="1"/><circle cx="165" cy="101" r="1"/><circle cx="189" cy="111" r="1"/><circle cx="214" cy="71" r="1"/><circle cx="238" cy="81" r="1"/><circle cx="263" cy="91" r="1"/><circle cx="287" cy="71" r="1"/></g>
    <g fill="var(--navy)"><circle cx="18" cy="111" r="1.1"/><circle cx="42" cy="101" r="1.1"/><circle cx="67" cy="111" r="1.1"/><circle cx="91" cy="81" r="1.1"/><circle cx="116" cy="81" r="1.1"/><circle cx="140" cy="91" r="1.1"/><circle cx="165" cy="81" r="1.1"/><circle cx="189" cy="81" r="1.1"/><circle cx="214" cy="64" r="1.1"/><circle cx="238" cy="61" r="1.1"/><circle cx="263" cy="61" r="1.1"/><circle cx="287" cy="64" r="1.1"/><circle cx="311" cy="61" r="1.1"/></g>
    <g font-size="2.5" fill="#555" text-anchor="middle">
      <text x="31" y="156">JAN</text><text x="55" y="156">FEB</text><text x="79" y="156">MAR</text><text x="104" y="156">APR</text><text x="128" y="156">MAY</text><text x="152" y="156">JUN</text><text x="177" y="156">JUL</text><text x="201" y="156">AUG</text><text x="225" y="156">SEP</text><text x="250" y="156">OCT</text><text x="274" y="156">NOV</text><text x="298" y="156">DEC</text>
    </g>
  </svg>
  <div class="footer-rule"></div>
  <div class="brand footer-brand"><span class="dot"></span>Velomar</div>
</section>

<!-- Row 5 -->
<section class="slide col1 row5">
  <h2 class="heading">Heading Goes Here</h2>
  <div class="sub" style="left:11px;top:32px">Stacked Chart</div>
  <svg class="abs" style="left:0;top:0" width="325" height="183" viewBox="0 0 325 183" font-family="Poppins, sans-serif">
    <line x1="11" y1="42" x2="312" y2="42" stroke="#e6e6e6" stroke-width=".5"/>
    <circle cx="242" cy="48" r="1.7" fill="var(--navy)"/><text x="245" y="49.3" font-size="3.6" fill="#444">Receipts</text>
    <circle cx="269" cy="48" r="1.7" fill="var(--green)"/><text x="272" y="49.3" font-size="3.6" fill="#444">Sales</text>
    <circle cx="291" cy="48" r="1.7" fill="var(--green-pale)"/><text x="294" y="49.3" font-size="3.6" fill="#444">Orders</text>
    <g stroke="#eeeeee" stroke-width=".4">
      <line x1="17" y1="53" x2="310" y2="53"/><line x1="17" y1="63" x2="310" y2="63"/><line x1="17" y1="73" x2="310" y2="73"/><line x1="17" y1="83" x2="310" y2="83"/><line x1="17" y1="93" x2="310" y2="93"/><line x1="17" y1="103" x2="310" y2="103"/><line x1="17" y1="113" x2="310" y2="113"/><line x1="17" y1="123" x2="310" y2="123"/><line x1="17" y1="133" x2="310" y2="133"/><line x1="17" y1="143" x2="310" y2="143"/><line x1="17" y1="153" x2="310" y2="153"/>
    </g>
    <g font-size="2.6" fill="#555" text-anchor="end">
      <text x="15" y="54">100</text><text x="15" y="64">90</text><text x="15" y="74">80</text><text x="15" y="84">70</text><text x="15" y="94">60</text><text x="15" y="104">50</text><text x="15" y="114">40</text><text x="15" y="124">30</text><text x="15" y="134">20</text><text x="15" y="144">10</text><text x="15" y="154">0</text>
    </g>
    <!-- bars: orders (pale), sales (green), receipts (navy); 1 unit = 1px -->
    <g>
      <rect x="23" y="143" width="14" height="10" fill="var(--green-pale)"/><rect x="23" y="133" width="14" height="10" fill="var(--green)"/><rect x="23" y="123" width="14" height="10" fill="var(--navy)"/>
      <rect x="48" y="123" width="14" height="30" fill="var(--green-pale)"/><rect x="48" y="93" width="14" height="30" fill="var(--green)"/><rect x="48" y="63" width="14" height="30" fill="var(--navy)"/>
      <rect x="72" y="140" width="14" height="13" fill="var(--green-pale)"/><rect x="72" y="127" width="14" height="13" fill="var(--green)"/><rect x="72" y="93" width="14" height="34" fill="var(--navy)"/>
      <rect x="97" y="136" width="14" height="17" fill="var(--green-pale)"/><rect x="97" y="70" width="14" height="66" fill="var(--green)"/><rect x="97" y="53" width="14" height="17" fill="var(--navy)"/>
      <rect x="121" y="113" width="14" height="40" fill="var(--green-pale)"/><rect x="121" y="93" width="14" height="20" fill="var(--green)"/><rect x="121" y="73" width="14" height="20" fill="var(--navy)"/>
      <rect x="145" y="140" width="14" height="13" fill="var(--green-pale)"/><rect x="145" y="126" width="14" height="14" fill="var(--green)"/>
      <rect x="170" y="126" width="14" height="27" fill="var(--green-pale)"/><rect x="170" y="99" width="14" height="27" fill="var(--green)"/><rect x="170" y="73" width="14" height="26" fill="var(--navy)"/>
      <rect x="194" y="133" width="14" height="20" fill="var(--green-pale)"/><rect x="194" y="113" width="14" height="20" fill="var(--green)"/><rect x="194" y="63" width="14" height="50" fill="var(--navy)"/>
      <rect x="219" y="140" width="14" height="13" fill="var(--green-pale)"/><rect x="219" y="126" width="14" height="14" fill="var(--green)"/><rect x="219" y="103" width="14" height="23" fill="var(--navy)"/>
      <rect x="243" y="118" width="14" height="35" fill="var(--green-pale)"/><rect x="243" y="83" width="14" height="35" fill="var(--green)"/>
      <rect x="268" y="126" width="14" height="27" fill="var(--green-pale)"/><rect x="268" y="99" width="14" height="27" fill="var(--green)"/><rect x="268" y="73" width="14" height="26" fill="var(--navy)"/>
      <rect x="292" y="140" width="14" height="13" fill="var(--green-pale)"/><rect x="292" y="126" width="14" height="14" fill="var(--green)"/><rect x="292" y="113" width="14" height="13" fill="var(--navy)"/>
    </g>
    <g font-size="2.5" fill="#555" text-anchor="middle">
      <text x="30" y="158">JAN</text><text x="55" y="158">FEB</text><text x="79" y="158">MAR</text><text x="104" y="158">APR</text><text x="128" y="158">MAY</text><text x="152" y="158">JUN</text><text x="177" y="158">JUL</text><text x="201" y="158">AUG</text><text x="226" y="158">SEP</text><text x="250" y="158">OCT</text><text x="275" y="158">NOV</text><text x="299" y="158">DEC</text>
    </g>
  </svg>
  <div class="footer-rule"></div>
  <div class="brand footer-brand"><span class="dot"></span>Velomar</div>
</section>

<section class="slide col2 row5">
  <div class="proc-title">PROCESS<small>INFOGRAPHIC</small></div>
  <svg class="abs" style="left:0;top:0" width="325" height="183" viewBox="0 0 325 183" font-family="Poppins, sans-serif">
    <defs>
      <marker id="arrG" markerWidth="5" markerHeight="5" refX="2.5" refY="2.5" orient="auto"><path d="M0,0L5,2.5L0,5Z" fill="var(--green)"/></marker>
      <marker id="arrN" markerWidth="5" markerHeight="5" refX="2.5" refY="2.5" orient="auto"><path d="M0,0L5,2.5L0,5Z" fill="var(--navy)"/></marker>
    </defs>
    <path d="M84,82 Q100,55 117,80" fill="none" stroke="var(--green)" stroke-width="1.8" marker-end="url(#arrG)"/>
    <path d="M141,82 Q157,55 174,80" fill="none" stroke="var(--navy)" stroke-width="1.8" marker-end="url(#arrN)"/>
    <path d="M198,82 Q214,55 231,80" fill="none" stroke="var(--green)" stroke-width="1.8" marker-end="url(#arrG)"/>
    <path d="M45,83 H103 V90 a6,6 0 0 1 0,12 V109 H45 V102 a6,6 0 0 0 0,-12 Z" fill="var(--green)"/>
    <path d="M103,83 H160 V90 a6,6 0 0 1 0,12 V109 H103 V102 a6,6 0 0 0 0,-12 Z" fill="var(--navy)"/>
    <path d="M160,83 H218 V90 a6,6 0 0 1 0,12 V109 H160 V102 a6,6 0 0 0 0,-12 Z" fill="var(--green)"/>
    <path d="M218,83 H275 V90 a6,6 0 0 1 0,12 V109 H218 V102 a6,6 0 0 0 0,-12 Z" fill="var(--navy)"/>
    <g font-size="11" font-weight="500" fill="#fff"><text x="55" y="100">01</text><text x="113" y="100">02</text><text x="170" y="100">03</text><text x="228" y="100">04</text></g>
  </svg>
  <div class="step-label" style="left:49px;top:114px"><b>LOREM IPSUM</b><span>Lorem ipsum dolor sit amet consectetur adipiscing elit. Duis elit sapien.</span></div>
  <div class="step-label" style="left:106px;top:114px"><b>LOREM IPSUM</b><span>Lorem ipsum dolor sit amet consectetur adipiscing elit. Duis elit sapien.</span></div>
  <div class="step-label" style="left:164px;top:114px"><b>LOREM IPSUM</b><span>Lorem ipsum dolor sit amet consectetur adipiscing elit. Duis elit sapien.</span></div>
  <div class="step-label" style="left:222px;top:114px"><b>LOREM IPSUM</b><span>Lorem ipsum dolor sit amet consectetur adipiscing elit. Duis elit sapien.</span></div>
  <div class="footer-rule"></div>
  <div class="brand footer-brand"><span class="dot"></span>Velomar</div>
</section>

<section class="slide col3 row5">
  <div class="proc-title">PROCESS<small>INFOGRAPHIC</small></div>
  <svg class="abs" style="left:0;top:0" width="325" height="183" viewBox="0 0 325 183" font-family="Poppins, sans-serif">
    <g fill="none" stroke="#b9dcd0" stroke-width=".8">
      <path d="M74,73 V62 H126 V73"/><path d="M137,73 V62 H189 V73"/><path d="M199,73 V62 H251 V73"/>
    </g>
    <g fill="var(--card)">
      <rect x="51" y="96" width="37" height="56"/><rect x="114" y="96" width="37" height="56"/><rect x="176" y="96" width="37" height="56"/><rect x="238" y="96" width="37" height="56"/>
    </g>
    <polygon points="69,71 91,83.5 91,108.5 69,121 47,108.5 47,83.5" fill="#fff"/>
    <polygon points="69,74 88,85 88,107 69,118 50,107 50,85" fill="var(--navy)"/>
    <polygon points="132,71 154,83.5 154,108.5 132,121 110,108.5 110,83.5" fill="var(--green-pale)"/>
    <polygon points="132,74 151,85 151,107 132,118 113,107 113,85" fill="var(--green)"/>
    <polygon points="194,71 216,83.5 216,108.5 194,121 172,108.5 172,83.5" fill="#fff"/>
    <polygon points="194,74 213,85 213,107 194,118 175,107 175,85" fill="var(--navy)"/>
    <polygon points="257,71 279,83.5 279,108.5 257,121 235,108.5 235,83.5" fill="var(--green-pale)"/>
    <polygon points="257,74 276,85 276,107 257,118 238,107 238,85" fill="var(--green)"/>
    <g font-size="17" font-weight="500" fill="#fff" text-anchor="middle"><text x="69" y="102">01</text><text x="132" y="102">02</text><text x="194" y="102">03</text><text x="257" y="102">04</text></g>
  </svg>
  <div class="step-label" style="left:44px;top:124px"><b>LOREM IPSUM</b><span>Lorem ipsum dolor sit amet consectetur adipiscing elit. Duis elit sapien.</span></div>
  <div class="step-label" style="left:107px;top:124px"><b>LOREM IPSUM</b><span>Lorem ipsum dolor sit amet consectetur adipiscing elit. Duis elit sapien.</span></div>
  <div class="step-label" style="left:169px;top:124px"><b>LOREM IPSUM</b><span>Lorem ipsum dolor sit amet consectetur adipiscing elit. Duis elit sapien.</span></div>
  <div class="step-label" style="left:232px;top:124px"><b>LOREM IPSUM</b><span>Lorem ipsum dolor sit amet consectetur adipiscing elit. Duis elit sapien.</span></div>
  <div class="footer-rule"></div>
  <div class="brand footer-brand"><span class="dot"></span>Velomar</div>
</section>

</main>
</body>
</html>
```